Webdesign Metall- und Stahlbau Verhoelt GmbH
Zielgruppe
Metall- und Stahlbau Verhoelt GmbH
Zielgruppe: öffentlicher Bereich, Industrie, Gesundheitswesen > deutschlandweit tätig
Aufgabenstellung
keine bewegten Bilder oder Elemente in der Website
klassisches Layout
sehr konservativ

```html
<!DOCTYPE html>
<html lang="de">
<head>
<meta charset="utf-8">
<title>Metall- und Stahlbau Verhoelt GmbH</title>
<link href="https://fonts.googleapis.com/css2?family=Inter:wght@400;500;600;700&display=swap" rel="stylesheet">
<style>
:root{
  --blue:#1e40af;
  --navy:#0f172a;
  --ink:#0f172a;
  --text:#475569;
  --muted:#64748b;
  --line:#e2e8f0;
  --soft:#f8fafc;
  --yellow:#fef9c3;
  --white:#ffffff;
}
*{box-sizing:border-box;margin:0;padding:0}
html,body{width:1200px;height:2667px;overflow:hidden}
body{font-family:"Inter",sans-serif;color:var(--ink);background:var(--white)}
.wrap{width:1020px;margin:0 auto;position:relative}
svg{display:block}

.topbar{height:31px;background:var(--blue);color:#fff;font-size:12px;font-weight:500}
.topbar .wrap{display:flex;justify-content:space-between;align-items:center;height:31px}
.topbar .contact{display:flex;gap:14px}
.topbar .contact span{display:flex;align-items:center;gap:6px}
.topbar .note{color:#dbeafe}

.header{height:80px;border-bottom:1px solid var(--line)}
.header .wrap{display:flex;justify-content:space-between;align-items:center;height:80px}
.brand{display:flex;align-items:center;gap:10px;font-size:17px;font-weight:700;color:var(--ink)}
.brand i{width:22px;height:22px;background:var(--blue);display:block}
.nav{display:flex;gap:27px;font-size:14px;color:#334155}
.nav .active{color:var(--ink);font-weight:500}

.hero{height:619px;background:var(--soft);border-bottom:1px solid var(--line)}
.hero .wrap{padding-top:107px}
.hero-text{width:470px}
.pill{display:inline-flex;align-items:center;gap:7px;font-size:12px;font-weight:500;color:var(--blue);background:#eff6ff;border:1px solid #dbeafe;border-radius:20px;padding:4px 11px}
.pill::before{content:"";width:6px;height:6px;border-radius:50%;background:var(--blue)}
.hero h1{font-size:42px;line-height:40px;font-weight:700;letter-spacing:-1px;margin-top:18px}
.hero p{font-size:17px;line-height:27.5px;color:var(--text);margin-top:24px}
.btns{display:flex;gap:13px;margin-top:28px}
.btn{height:42px;padding:0 21px;display:flex;align-items:center;font-size:14px;font-weight:500}
.btn.primary{background:var(--blue);color:#fff}
.btn.ghost{background:#fff;border:1px solid #cbd5e1;color:var(--ink)}
.hero-photo{position:absolute;right:0;top:107px;width:482px;height:403px;background:linear-gradient(120deg,#9ca3af,#4b5563 55%,#1f2937)}

.facts{height:195px;border-bottom:1px solid var(--line)}
.facts .wrap{display:flex;padding-top:40px}
.fact{flex:1;padding:0 14px;border-left:1px solid var(--line);height:115px}
.fact:first-child{border-left:none}
.fact h3{font-size:15px;font-weight:600;margin-top:12px}
.fact p{font-size:13px;line-height:20px;color:var(--muted);margin-top:6px;width:300px}

.services{height:874px;background:var(--soft);border-bottom:1px solid var(--line)}
.services .wrap{padding-top:82px}
h2{font-size:26px;font-weight:600;letter-spacing:-.5px}
.lead{font-size:17px;line-height:24px;color:var(--text);margin-top:16px;width:520px}
.grid{display:grid;grid-template-columns:repeat(3,321px);gap:27px 28px;margin-top:55px}
.card{background:#fff;border:1px solid var(--line);padding:27px 27px;min-height:247px}
.grid .card:nth-child(-n+3){min-height:272px}
.icon{width:40px;height:40px;background:var(--yellow);display:flex;align-items:center;justify-content:center}
.card h3{font-size:17px;font-weight:600;margin-top:21px}
.card p{font-size:15px;line-height:24.5px;color:var(--text);margin-top:14px}
.card.feature{background:var(--blue);border-color:var(--blue)}
.card.feature .icon{background:rgba(255,255,255,.12)}
.card.feature h3{color:#fff}
.card.feature p{color:#dbeafe}

.groups{height:521px}
.groups .wrap{padding-top:81px;display:flex;justify-content:space-between}
.groups-left{width:470px}
.groups-left .lead{width:470px}
.list{margin-top:36px}
.item{display:flex;gap:16px;margin-bottom:23px}
.item h4{font-size:15px;font-weight:500}
.item p{font-size:13px;color:var(--text);margin-top:4px}
.panel{width:483px;height:359px;background:var(--soft);border:1px solid var(--line);padding:27px}
.panel h3{font-size:20px;font-weight:600;letter-spacing:-.3px}
.panel p{font-size:15px;line-height:24px;color:var(--text);margin-top:20px}
.panel p b{color:#334155}
.panel hr{border:none;border-top:1px solid var(--line);margin:24px 0 20px}
.certs-label{font-size:12px;letter-spacing:1px;color:var(--muted);font-weight:500}
.certs{display:flex;gap:14px;margin-top:9px}
.cert{width:92px;height:25px;border:1px solid #cbd5e1;background:#fff}
.cert+.cert{width:74px}

.footer{height:347px;background:var(--navy);color:#cbd5e1}
.footer .wrap{padding-top:56px}
.foot-cols{display:flex}
.foot-brand{width:530px}
.foot-brand .brand{color:#fff}
.foot-brand .brand i{background:#facc15}
.foot-brand p{font-size:13px;line-height:20px;margin-top:26px;color:#cbd5e1}
.foot-col{width:265px}
.foot-col h4{font-size:15px;font-weight:600;color:#fff;margin-bottom:18px}
.foot-col .row{display:flex;gap:10px;font-size:13px;line-height:20px;margin-bottom:10px}
.foot-col a{display:block;font-size:13px;color:#cbd5e1;text-decoration:none;margin-bottom:11px}
.foot-bottom{border-top:1px solid #1e293b;margin-top:68px;padding-top:30px;display:flex;justify-content:space-between;font-size:12px;color:#64748b}
</style>
</head>
<body>

<div class="topbar">
  <div class="wrap">
    <div class="contact">
      <span><svg width="13" height="13" viewBox="0 0 24 24" fill="none" stroke="#facc15" stroke-width="2"><path d="M22 16.9v3a2 2 0 0 1-2.2 2 19.8 19.8 0 0 1-8.6-3.1 19.5 19.5 0 0 1-6-6A19.8 19.8 0 0 1 2.1 4.2 2 2 0 0 1 4.1 2h3a2 2 0 0 1 2 1.7c.1 1 .4 1.9.7 2.8a2 2 0 0 1-.5 2.1L8 9.9a16 16 0 0 0 6 6l1.3-1.3a2 2 0 0 1 2.1-.4c.9.3 1.8.6 2.8.7a2 2 0 0 1 1.7 2z"/></svg>030 / 482 197 30</span>
      <span><svg width="13" height="13" viewBox="0 0 24 24" fill="none" stroke="#facc15" stroke-width="2"><rect x="2" y="4" width="20" height="16" rx="2"/><path d="m22 7-10 6L2 7"/></svg>kontakt@verhoelt-stahlbau.de</span>
    </div>
    <div class="note">Meisterbetrieb der Innung seit 1965</div>
  </div>
</div>

<header class="header">
  <div class="wrap">
    <div class="brand"><i></i>Metall- und Stahlbau Verhoelt GmbH</div>
    <nav class="nav">
      <span class="active">Startseite</span><span>Leistungen</span><span>Referenzen</span><span>Kontakt</span>
    </nav>
  </div>
</header>

<section class="hero">
  <div class="wrap">
    <div class="hero-text">
      <span class="pill">Deutschlandweit tätig</span>
      <h1>Präzision in Stahl und Metall<br>für Industrie und Öffentliche Hand.</h1>
      <p>Als erfahrener Meisterbetrieb realisieren wir seit über 50 Jahren anspruchsvolle Konstruktionen. Ihr Partner für Stahlbau, Metallbau und Edelstahlverarbeitung im Gesundheitswesen und Industriebau.</p>
      <div class="btns"><span class="btn primary">Projekt anfragen</span><span class="btn ghost">Unsere Leistungen</span></div>
    </div>
    <div class="hero-photo" role="img" aria-label="Schwarzweißfoto: Metallarbeiter schleift einen Stahlträger, Funken sprühen"></div>
  </div>
</section>

<section class="facts">
  <div class="wrap">
    <div class="fact">
      <svg width="24" height="24" viewBox="0 0 24 24" fill="none" stroke="#1e40af" stroke-width="2"><path d="M12 22s8-4 8-10V5l-8-3-8 3v7c0 6 8 10 8 10z"/><path d="m9 12 2 2 4-4"/></svg>
      <h3>Meisterbetrieb</h3>
      <p>Qualität und Sicherheit seit 1965 durch zertifizierte Handwerkskunst.</p>
    </div>
    <div class="fact">
      <svg width="24" height="24" viewBox="0 0 24 24" fill="none" stroke="#1e40af" stroke-width="2"><path d="M20 10c0 6-8 12-8 12s-8-6-8-12a8 8 0 0 1 16 0z"/><circle cx="12" cy="10" r="3"/></svg>
      <h3>Deutschlandweit</h3>
      <p>Wir betreuen Projekte im gesamten Bundesgebiet zuverlässig.</p>
    </div>
    <div class="fact">
      <svg width="26" height="24" viewBox="0 0 24 24" fill="none" stroke="#1e40af" stroke-width="2"><rect x="8" y="2" width="12" height="20" rx="1"/><path d="M8 10H4v12h4M12 6h4M12 10h4M12 14h4M12 18h4"/></svg>
      <h3>Öffentlicher Sektor</h3>
      <p>Spezialisiert auf Anforderungen von Behörden und Gesundheitswesen.</p>
    </div>
  </div>
</section>

<section class="services">
  <div class="wrap">
    <h2>Unser Leistungsspektrum</h2>
    <p class="lead">Wir verbinden traditionelles Handwerk mit moderner Fertigungstechnik. Langlebigkeit und Präzision stehen bei uns an erster Stelle.</p>
    <div class="grid">
      <div class="card">
        <div class="icon"><svg width="18" height="18" viewBox="0 0 24 24" fill="none" stroke="#1e40af" stroke-width="2"><path d="m15 12-8.5 8.5a2.1 2.1 0 0 1-3-3L12 9"/><path d="m17.6 15 4.4-4.4-7.6-7.6L10 7.4z"/></svg></div>
        <h3>Allgemeiner Stahlbau</h3>
        <p>Konstruktion, Fertigung und Montage von Stahltragwerken, Hallenbau und Sonderkonstruktionen nach DIN-Normen.</p>
      </div>
      <div class="card">
        <div class="icon"><svg width="18" height="18" viewBox="0 0 24 24" fill="none" stroke="#1e40af" stroke-width="2"><path d="M14.7 6.3a4 4 0 0 0 5 5l-8.4 8.4a2.1 2.1 0 0 1-3-3z"/><path d="M14.7 6.3 17 4l3 3-2.3 2.3"/></svg></div>
        <h3>Metallbau</h3>
        <p>Maßgeschneiderte Lösungen für Treppen, Geländer, Vordächer und Tore. Funktional und ästhetisch anspruchsvoll.</p>
      </div>
      <div class="card">
        <div class="icon"><svg width="18" height="18" viewBox="0 0 24 24" fill="none" stroke="#1e40af" stroke-width="2"><path d="M12 4l1.5 5L18 11l-4.5 2L12 18l-1.5-5L6 11l4.5-2z"/><path d="M19 3v4M17 5h4M5 17v4M3 19h4"/></svg></div>
        <h3>Edelstahlverarbeitung</h3>
        <p>Hygienische und korrosionsbeständige Konstruktionen, ideal für das Gesundheitswesen und Laboreinrichtungen.</p>
      </div>
      <div class="card">
        <div class="icon"><svg width="18" height="18" viewBox="0 0 24 24" fill="none" stroke="#1e40af" stroke-width="2"><path d="M3 21h18M6 21V4h10v17M16 4l3 2v15M13 12h.01"/></svg></div>
        <h3>Brandschutzelemente</h3>
        <p>Fertigung und Montage von Brandschutztüren und -toren für öffentliche Gebäude und Industrieanlagen.</p>
      </div>
      <div class="card">
        <div class="icon"><svg width="18" height="18" viewBox="0 0 24 24" fill="none" stroke="#1e40af" stroke-width="2"><rect x="5" y="4" width="14" height="18" rx="2"/><rect x="9" y="2" width="6" height="4" rx="1"/><path d="m9 14 2 2 4-4"/></svg></div>
        <h3>Wartung &amp; Instandhaltung</h3>
        <p>Regelmäßige Prüfung und Reparatur bestehender Anlagen zur Sicherung der Betriebsfähigkeit und Sicherheit.</p>
      </div>
      <div class="card feature">
        <div class="icon"><svg width="18" height="18" viewBox="0 0 24 24" fill="none" stroke="#facc15" stroke-width="2"><path d="M14 2H6a2 2 0 0 0-2 2v16a2 2 0 0 0 2 2h12a2 2 0 0 0 2-2V8z"/><path d="M14 2v6h6M8 13h8M8 17h8M8 9h2"/></svg></div>
        <h3>Beratung &amp; Planung</h3>
        <p>Wir unterstützen Architekten und Bauherren von der ersten Skizze bis zur statischen Berechnung.</p>
      </div>
    </div>
  </div>
</section>

<section class="groups">
  <div class="wrap">
    <div class="groups-left">
      <h2>Unsere Zielgruppen</h2>
      <p class="lead">Wir verstehen die spezifischen Anforderungen komplexer Bauvorhaben. Zu unseren langjährigen Auftraggebern zählen:</p>
      <div class="list">
        <div class="item"><svg width="18" height="18" viewBox="0 0 24 24" fill="none" stroke="#1e40af" stroke-width="2.2"><path d="M4 12l5 5L20 6"/></svg><div><h4>Öffentlicher Bereich</h4><p>Schulen, Behörden, Sportstätten und Verwaltungsgebäude.</p></div></div>
        <div class="item"><svg width="18" height="18" viewBox="0 0 24 24" fill="none" stroke="#1e40af" stroke-width="2.2"><path d="M4 12l5 5L20 6"/></svg><div><h4>Industrie &amp; Gewerbe</h4><p>Produktionshallen, Lagertechnik und Infrastruktur.</p></div></div>
        <div class="item"><svg width="18" height="18" viewBox="0 0 24 24" fill="none" stroke="#1e40af" stroke-width="2.2"><path d="M4 12l5 5L20 6"/></svg><div><h4>Gesundheitswesen</h4><p>Kliniken, Pflegeheime und Labore (hohe Hygieneanforderungen).</p></div></div>
      </div>
    </div>
    <div class="panel">
      <h3>Ihr Projekt in guten Händen</h3>
      <p>Die Verhoelt GmbH steht für Termintreue und solide Handwerksarbeit. Wir verzichten auf unnötigen Schnick-Schnack und konzentrieren uns auf das Wesentliche: <b>Das Ergebnis.</b></p>
      <p>Unsere Mitarbeiter werden regelmäßig geschult, um den aktuellen Normen im Stahlbau gerecht zu werden.</p>
      <hr>
      <div class="certs-label">ZERTIFIZIERUNGEN</div>
      <div class="certs"><span class="cert"></span><span class="cert"></span></div>
    </div>
  </div>
</section>

<footer class="footer">
  <div class="wrap">
    <div class="foot-cols">
      <div class="foot-brand">
        <div class="brand"><i></i>Metall- und Stahlbau Verhoelt GmbH</div>
        <p>Ihr zuverlässiger Partner für Stahlbau und<br>Metallverarbeitung.<br>Qualität aus Meisterhand seit 1965.</p>
      </div>
      <div class="foot-col">
        <h4>Kontakt</h4>
        <div class="row"><svg width="16" height="16" viewBox="0 0 24 24" fill="none" stroke="#94a3b8" stroke-width="2"><path d="M20 10c0 6-8 12-8 12s-8-6-8-12a8 8 0 0 1 16 0z"/><circle cx="12" cy="10" r="3"/></svg><span>Hüttenweg 27<br>44137 Dortmund</span></div>
        <div class="row"><svg width="16" height="16" viewBox="0 0 24 24" fill="none" stroke="#94a3b8" stroke-width="2"><path d="M22 16.9v3a2 2 0 0 1-2.2 2 19.8 19.8 0 0 1-8.6-3.1 19.5 19.5 0 0 1-6-6A19.8 19.8 0 0 1 2.1 4.2 2 2 0 0 1 4.1 2h3a2 2 0 0 1 2 1.7c.1 1 .4 1.9.7 2.8a2 2 0 0 1-.5 2.1L8 9.9a16 16 0 0 0 6 6l1.3-1.3a2 2 0 0 1 2.1-.4c.9.3 1.8.6 2.8.7a2 2 0 0 1 1.7 2z"/></svg><span>030 / 482 197 30</span></div>
        <div class="row"><svg width="16" height="16" viewBox="0 0 24 24" fill="none" stroke="#94a3b8" stroke-width="2"><rect x="2" y="4" width="20" height="16" rx="2"/><path d="m22 7-10 6L2 7"/></svg><span>kontakt@verhoelt-stahlbau.de</span></div>
      </div>
      <div class="foot-col">
        <h4>Rechtliches</h4>
        <a>Impressum</a><a>Datenschutz</a><a>AGB</a>
      </div>
    </div>
    <div class="foot-bottom">
      <span>© 2023 Metall- und Stahlbau Verhoelt GmbH. Alle Rechte vorbehalten.</span>
      <span>Handwerk mit Tradition.</span>
    </div>
  </div>
</footer>

</body>
</html>
```